Webdesign für berufliches Schulzentrum für Ernährung, Gastgewerbe, Gesundheit
Zielgruppe
Berufliches Schulzentrum für Ernährung, Gastgewerbe, Gesundheit
Zielgruppe: Schüler und Auszubildende
Aufgabenstellung
- modernes, aber dennoch strukturiertes Aussehen der Webseite
- einfache Navigation
- die beiden Grüntöne aus dem Logo sollen sich bitte in der Seite wiederfinden - jedoch in freundlicher Form

```html
<!DOCTYPE html>
<html lang="de">
<head>
<meta charset="utf-8">
<title>BSZ Lindenhain</title>
<link rel="stylesheet" href="https://fonts.googleapis.com/css2?family=Crimson+Text:wght@400;600;700&family=Caveat:wght@400&display=swap">
<style>
:root{
  --green-dark:#17361f;
  --green-mint:#b9e6c7;
  --green-mid:#7fb893;
  --grey-bg:#efefef;
  --text:#2b2b2b;
  --white:#ffffff;
}
*{margin:0;padding:0;box-sizing:border-box}
html,body{width:1200px;height:5026px;overflow:hidden}
body{position:relative;background:var(--white);color:var(--text);font-family:"Crimson Text",Georgia,serif}
.btn{position:absolute;display:flex;align-items:center;justify-content:center;border:3px solid var(--green-dark);color:var(--green-dark);font-size:19px;background:transparent}
.photo{position:absolute}
.script{font-family:"Caveat",cursive;color:var(--green-mint);font-size:72px;line-height:1}

/* header */
.site-header{position:absolute;top:0;left:0;width:1200px;height:182px;background:var(--white)}
.brand{position:absolute;left:74px;top:70px;display:flex;align-items:center;gap:12px;font-size:30px;font-weight:700;color:var(--green-dark)}
.brand-mark{width:26px;height:26px;background:var(--green-mint)}
.main-nav{position:absolute;right:74px;top:84px;display:flex;gap:28px;font-size:15px;color:#555}
.main-nav .caret{color:var(--green-mint);font-size:11px;margin-left:4px}

/* hero */
.hero{position:absolute;top:182px;left:0;width:1200px;height:493px;background:linear-gradient(180deg,#8e968f 0%,#7b8a80 50%,#6f7c71 100%)}
.hero-title{position:absolute;width:100%;top:180px;text-align:center;color:var(--white);font-size:80px;font-weight:400;line-height:1;text-shadow:0 2px 6px rgba(0,0,0,.3)}
.hero-sub{position:absolute;width:100%;top:270px;text-align:center;color:var(--white);font-size:42px;text-shadow:0 2px 6px rgba(0,0,0,.3)}

/* ausschreibung */
.tender{position:absolute;top:675px;left:0;width:1200px;height:365px;background:var(--green-mint)}
.tender h2{position:absolute;left:72px;top:48px;font-size:46px;font-weight:400;color:var(--green-dark)}
.tender h3{position:absolute;left:75px;top:128px;width:680px;font-size:30px;line-height:38px;font-weight:700;color:var(--green-dark)}
.tender p{position:absolute;left:75px;top:240px;width:680px;font-size:19px;line-height:28px}

/* section heads */
.section-head{position:absolute;left:0;width:1200px;height:90px;text-align:center}
.section-head .lead{position:absolute;width:100%;top:8px;font-size:42px;line-height:1;color:var(--green-dark)}
.section-head .script{position:absolute;width:100%;top:22px}

/* school types */
.type-card{position:absolute;top:1254px;width:332px}
.type-card .photo{position:relative;width:332px;height:332px}
.type-card .label{height:67px;background:var(--green-dark);color:var(--white);font-size:26px;display:flex;align-items:center;justify-content:center}

/* plans */
.plans-bg{position:absolute;top:1853px;left:0}
.plans h2{position:absolute;right:74px;top:1910px;font-size:46px;font-weight:400;color:var(--green-dark)}
.plans p{position:absolute;right:78px;top:2000px;width:680px;text-align:right;font-size:19px;line-height:28px;color:#444}
.plans .link{position:absolute;left:728px;top:2148px;font-size:19px;color:var(--green-dark)}

/* news */
.news-card{position:absolute;top:2562px;width:296px;height:563px;background:var(--white);box-shadow:0 8px 24px rgba(0,0,0,.10)}
.news-card .photo{position:relative;width:296px;height:292px}
.news-card h3{position:absolute;left:27px;top:320px;font-size:29px;font-weight:400;color:var(--green-dark)}
.news-card p{position:absolute;left:27px;top:380px;width:245px;font-size:18px;line-height:26px;color:#666}
.news-card .meta{position:absolute;left:27px;right:24px;top:496px;border-top:2px solid var(--green-dark);padding-top:18px;display:flex;justify-content:space-between;font-size:12px;color:var(--green-dark)}

/* enrollment */
.enroll{position:absolute;top:3245px;left:0;width:1200px;height:365px;background:var(--green-dark);color:var(--white);text-align:center}
.enroll h2{position:absolute;width:100%;top:44px;font-size:42px;font-weight:400;color:var(--green-mint)}
.enroll h3{position:absolute;width:100%;top:140px;font-size:30px;font-weight:700}
.enroll p{position:absolute;width:100%;top:212px;font-size:20px}
.enroll .btn{left:478px;top:277px;width:244px;height:48px;border-color:var(--green-mint);color:var(--white)}

/* support */
.support h3{position:absolute;left:75px;top:3906px;font-size:29px;font-weight:700;color:var(--green-dark)}
.support p{position:absolute;left:75px;top:3990px;width:500px;font-size:19px;line-height:28px}

/* impressions */
.imp-title{position:absolute;width:1200px;top:4305px;text-align:center;font-size:46px;font-weight:400;color:var(--green-dark)}
.quote{position:absolute;top:4423px;width:421px;height:230px;background:var(--green-mint);padding:44px 32px 0 32px}
.quote p{font-size:18px;line-height:26px;color:#444}
.quote .name{position:absolute;right:32px;bottom:22px;font-size:19px;color:var(--green-dark)}
.arrow{position:absolute;top:4524px}

/* footer */
.site-footer{position:absolute;top:4750px;left:0;width:1200px;height:276px;background:var(--green-dark);color:var(--white);font-size:15px}
.f-col{position:absolute;top:82px;line-height:30px}
.f-col strong{font-weight:700}
.f-row{display:flex;align-items:center;gap:12px}
.f-rule{position:absolute;left:74px;right:74px;top:219px;border-top:1px solid var(--green-mint)}
.f-copy{position:absolute;left:74px;top:232px;font-size:13px}
.f-legal{position:absolute;right:74px;top:232px;font-size:13px;display:flex;gap:22px}
</style>
</head>
<body>

<header class="site-header">
  <div class="brand"><span class="brand-mark"></span>BSZ Lindenhain</div>
  <nav class="main-nav">
    <span>Schularten<span class="caret">▼</span></span>
    <span>Pläne &amp; Termine</span>
    <span>Aktuelles</span>
    <span>Schulanmeldung</span>
    <span>Förderverein</span>
    <span>Impressionen</span>
    <span>Kontakt</span>
  </nav>
</header>

<section class="hero" role="img" aria-label="Schulgebäude mit Bäumen, grau-grün getönt">
  <h1 class="hero-title">BSZ für</h1>
  <div class="hero-sub">Ernährung, Gastgewerbe, Gesundheit!</div>
</section>

<section class="tender">
  <h2>Ausschreibung</h2>
  <h3>Attraktive und moderne Warenpräsentation im Verkauf</h3>
  <p>Wir suchen zur Ergänzung unseres schulischen Angebots für die Berufsausbildung Fachverkäufer/-in Backwaren Experten/ Expertinnen</p>
  <div class="btn" style="left:883px;top:183px;width:244px;height:48px">Mehr Erfaren</div>
</section>

<div class="section-head" style="top:1116px">
  <div class="lead">Unsere</div>
  <div class="script">Schularten</div>
</div>

<div class="type-card" style="left:74px">
  <div class="photo" role="img" aria-label="Frau mit Backblech in einer Küche" style="background:linear-gradient(135deg,#a4785e,#d9cfc4)"></div>
  <div class="label">Berufsschule</div>
</div>
<div class="type-card" style="left:433px">
  <div class="photo" role="img" aria-label="Frau im Laborkittel am Laptop" style="background:linear-gradient(135deg,#d9dde0,#8fa7b8)"></div>
  <div class="label">Berufsfachschule</div>
</div>
<div class="type-card" style="left:792px">
  <div class="photo" role="img" aria-label="Schüler rechnet mit Taschenrechner" style="background:linear-gradient(135deg,#5c6f86,#c9c6c0)"></div>
  <div class="label">Berufsvorbereitung</div>
</div>
<div class="btn" style="left:121px;top:1688px;width:242px;height:48px">Mehr Erfaren</div>
<div class="btn" style="left:479px;top:1688px;width:242px;height:48px">Mehr Erfaren</div>
<div class="btn" style="left:837px;top:1688px;width:242px;height:48px">Mehr Erfaren</div>

<svg class="plans-bg" width="1200" height="950" viewBox="0 0 1200 950" aria-hidden="true">
  <rect width="1200" height="950" fill="#efefef"/>
  <polygon points="0,582 351,342 1200,907 1200,950 0,950" fill="#ffffff"/>
  <polygon points="878,645 1116,489 1200,547 1200,937" fill="#b9e6c7"/>
</svg>
<div class="photo" role="img" aria-label="Klemmbrett mit Checkliste Pläne und Termine" style="left:88px;top:1916px;width:263px;height:415px;background:linear-gradient(180deg,#e9e4dc,#eef6f0)"></div>

<section class="plans">
  <h2>Pläne &amp; Termine</h2>
  <p>Lorem ipsum dolor sit amet, consectetur adipiscing elit, sed do eiusmod tempor incididunt ut labore et dolore magna aliqua. Ut enim ad minim veniam, quis nostrud exercitation ullamco laboris nisi ut aliquip</p>
  <span class="link">Blockpläne</span>
  <div class="btn" style="left:882px;top:2136px;width:244px;height:49px">Nachschreibetermine</div>
</section>

<div class="section-head" style="top:2404px">
  <div class="lead">Alles</div>
  <div class="script">Aktuelles</div>
</div>

<article class="news-card" style="left:137px">
  <div class="photo" role="img" aria-label="Verschiedene Brote und Brötchen" style="background:linear-gradient(135deg,#c89a62,#7a5538)"></div>
  <h3>Lorem Ipsum</h3>
  <p>Lorem ipsum dolor sit amet, consectetur adipiscing elit, sed do eiusmod tempor incididunt ut labore</p>
  <div class="meta"><span>02.04.2024</span><span>by John Doe</span></div>
</article>
<article class="news-card" style="left:453px">
  <div class="photo" role="img" aria-label="Laborkolben mit farbiger Flüssigkeit" style="background:linear-gradient(135deg,#6aa6d8,#2f6fb4)"></div>
  <h3>Lorem Ipsum</h3>
  <p>Lorem ipsum dolor sit amet, consectetur adipiscing elit, sed do eiusmod tempor incididunt ut labore</p>
  <div class="meta"><span>02.04.2024</span><span>by John Doe</span></div>
</article>
<article class="news-card" style="left:767px">
  <div class="photo" role="img" aria-label="Pflegeschüler im Klinikflur" style="background:linear-gradient(135deg,#4e5a64,#dfe3e6)"></div>
  <h3>Lorem Ipsum</h3>
  <p>Lorem ipsum dolor sit amet, consectetur adipiscing elit, sed do eiusmod tempor incididunt ut labore</p>
  <div class="meta"><span>02.04.2024</span><span>by John Doe</span></div>
</article>

<section class="enroll">
  <h2>Schulanmeldung</h2>
  <h3>Du möchtest gern Schüler an unserer Schule werden?</h3>
  <p>Dann findest Du hier die entsprechenden Anmeldeformulare.</p>
  <div class="btn">Jetzt Bewerben</div>
</section>
<div class="photo" role="img" aria-label="Lächelnde Lehrerin zeigt zur Seite" style="left:0;top:3268px;width:255px;height:342px;background:linear-gradient(180deg,#2c4a34,#5f7c8e)"></div>
<div class="photo" role="img" aria-label="Schüler mit Mappe und Kopfhörern" style="left:955px;top:3200px;width:245px;height:410px;background:linear-gradient(180deg,#3f5a75,#2d4b6b)"></div>

<div class="section-head" style="top:3722px">
  <div class="lead">Unsere</div>
  <div class="script">Förderverein</div>
</div>
<section class="support">
  <h3>Freunde und Förderer</h3>
  <p>des Beruflichen Schulzentrums Lindenhain e. V.' ... Möchtest auch du unser berufliches Schulzentrum unterstützen?</p>
  <div class="btn" style="left:74px;top:4123px;width:242px;height:48px">Mehr Erfaren</div>
</section>
<div class="photo" role="img" aria-label="Viele Hände halten gemeinsam ein Herz" style="left:613px;top:3873px;width:587px;height:331px;background:linear-gradient(135deg,#ece8e2,#ddd5cc)"></div>

<h2 class="imp-title">Impressionen</h2>
<svg class="arrow" style="left:100px" width="16" height="24" viewBox="0 0 16 24" aria-hidden="true"><path d="M12 2 L3 12 L12 22" fill="none" stroke="#17361f" stroke-width="2.5"/></svg>
<svg class="arrow" style="left:1083px" width="16" height="24" viewBox="0 0 16 24" aria-hidden="true"><path d="M4 2 L13 12 L4 22" fill="none" stroke="#17361f" stroke-width="2.5"/></svg>
<blockquote class="quote" style="left:164px">
  <p>“Lorem ipsum dolor sit amet, consectetur adipiscing elit, sed do eiusmod tempor incididunt ut labore”</p>
  <span class="name">Lena Fischer</span>
</blockquote>
<blockquote class="quote" style="left:613px">
  <p>Sed ut perspiciatis unde omnis iste natus error sit voluptatem accusantium doloremque laudantium, totam rem aperiam, eaque ipsa quae ab illo inventore veritatis et quasi architecto beatae vitae dicta sunt explicabo.</p>
  <span class="name">Jonas Weber</span>
</blockquote>

<footer class="site-footer">
  <div class="f-col" style="left:74px">
    <strong>BSZ Lindenhain for nutrition, hospitality, health</strong><br>
    01234 Lindenhain<br>
    Am Wiesengrund 8
  </div>
  <div class="f-col" style="left:507px">
    <div class="f-row"><svg width="15" height="15" viewBox="0 0 24 24" aria-hidden="true"><path d="M6.6 10.8a15 15 0 0 0 6.6 6.6l2.2-2.2a1 1 0 0 1 1-.25 11.4 11.4 0 0 0 3.6.57 1 1 0 0 1 1 1V20a1 1 0 0 1-1 1A17 17 0 0 1 3 4a1 1 0 0 1 1-1h3.5a1 1 0 0 1 1 1c0 1.250.2 2.45.57 3.57a1 1 0 0 1-.25 1z" fill="#fff"/></svg>0123/45678-0</div>
    <div class="f-row"><svg width="15" height="15" viewBox="0 0 24 24" aria-hidden="true"><rect x="6" y="2" width="12" height="6" fill="#fff"/><rect x="2" y="9" width="20" height="9" rx="2" fill="#fff"/><rect x="6" y="15" width="12" height="7" fill="#fff" stroke="#17361f" stroke-width="1.5"/></svg>0123/45678-42</div>
    <div class="f-row"><svg width="15" height="15" viewBox="0 0 24 24" aria-hidden="true"><rect x="2" y="5" width="20" height="14" fill="#fff"/><path d="M2 5 L12 13 L22 5" fill="none" stroke="#17361f" stroke-width="1.6"/></svg>info@bsz-lindenhain.example</div>
  </div>
  <div class="f-col" style="left:761px">
    <strong>Authorized representatives</strong><br>
    Ms. A. Berger (headmistress)<br>
    Ms. K. Lorenz (deputy)
  </div>
  <div class="f-rule"></div>
  <div class="f-copy">© 2024 Copyright BSZ</div>
  <div class="f-legal"><span>Impressum</span><span>Kontakt</span><span>Datenschutz</span></div>
</footer>

</body>
</html>
```